Tech business card design

We need an amazing business card design for our new business 'Pexla' a marketing tech startup based in Sydney, Australia. We provide an online marketplace for businesses to search and buy advertising media, connect with service providers and learn more about marketing. We wish to communicate 'cool tech', reliability and professionalism and design based around our logo.

Target Market(s)

Business Owners

Contact Information for Business Card

Name
Position
Email Address
Website
Phone Number

Font styles to use
Other font styles liked:
• Avenir & Avenir Next

Colors

Designer to choose colors to be used in the design.

```html
<!DOCTYPE html>
<html lang="en">
<head>
<meta charset="utf-8">
<title>Pexla Business Card</title>
<link rel="stylesheet" href="https://fonts.googleapis.com/css2?family=Open+Sans:wght@400;700;800&display=swap">
<style>
  :root {
    --stage: #e2dfdf;
    --navy: #12143a;
    --navy-light: #222650;
    --white: #ffffff;
    --back-fill: #dadae6;
    --edge: #d2d2d6;
  }
  * { margin: 0; padding: 0; box-sizing: border-box; }
  html, body { width: 975px; height: 1200px; overflow: hidden; }
  body {
    background: var(--stage);
    font-family: "Open Sans", sans-serif;
    position: relative;
  }
  .card {
    position: absolute;
    left: 56px;
    width: 864px;
    height: 496px;
    border-radius: 30px;
    overflow: hidden;
    border: 2px solid var(--edge);
  }
  .card--front { top: 86px; background: var(--white); }
  .card--back { top: 632px; background: var(--back-fill); border-width: 1px; }

  .diagonal { position: absolute; inset: 0; width: 100%; height: 100%; }

  .wordmark {
    position: absolute;
    font-weight: 800;
    color: var(--navy);
    letter-spacing: -2px;
    line-height: 1;
  }
  .card--front .wordmark { left: 40px; top: 176px; font-size: 128px; }
  .card--back .wordmark {
    left: 0; right: 0; text-align: center;
    top: 138px; font-size: 168px;
  }

  .contact {
    position: absolute;
    right: 54px;
    top: 158px;
    text-align: right;
    color: var(--white);
  }
  .contact__name { font-weight: 700; font-size: 26px; line-height: 32px; letter-spacing: 0.3px; }
  .contact__role { font-size: 23px; line-height: 34px; }
  .contact__lines { margin-top: 12px; }
  .contact__line {
    display: flex; justify-content: flex-end; align-items: center;
    gap: 6px; font-size: 19px; line-height: 33px;
  }
  .contact__line svg { width: 22px; height: 22px; flex: none; }
  .contact__address { margin-top: 12px; font-size: 19px; line-height: 29px; }

  .back-url {
    position: absolute;
    left: 0; right: 0; top: 386px;
    text-align: center;
    font-size: 25px;
    letter-spacing: 3px;
    color: var(--navy);
  }
</style>
</head>
<body>
  <section class="card card--front">
    <svg class="diagonal" viewBox="0 0 864 496" preserveAspectRatio="none" aria-hidden="true">
      <polygon points="59,496 864,-9 864,496" fill="var(--navy)"/>
      <polygon points="59,496 120,496 690,135 640,150" fill="var(--navy-light)"/>
    </svg>
    <div class="wordmark">pexla</div>
    <div class="contact">
      <div class="contact__name">SAM CARTER</div>
      <div class="contact__role">Position</div>
      <div class="contact__lines">
        <div class="contact__line">012-345-6789
          <svg viewBox="0 0 24 24" aria-hidden="true"><circle cx="12" cy="12" r="10.5" fill="none" stroke="#fff" stroke-width="1.8"/><path d="M8.2 6.8l1.8-.4 1.1 2.7-1.2 1a7 7 0 0 0 3.9 3.9l1-1.2 2.7 1.1-.4 1.8c-.2.6-.8 1-1.5.9A9 9 0 0 1 7.3 8.3c-.1-.7.3-1.3.9-1.5z" fill="#fff"/></svg>
        </div>
        <div class="contact__line">info@pexla.com
          <svg viewBox="0 0 24 24" aria-hidden="true"><rect x="2" y="5" width="20" height="14" fill="#fff"/><path d="M2 5l10 8 10-8M2 19l7.5-7M22 19l-7.5-7" stroke="var(--navy)" stroke-width="1.6" fill="none"/></svg>
        </div>
        <div class="contact__line">www.pexla.com
          <svg viewBox="0 0 24 24" aria-hidden="true" fill="none" stroke="#fff" stroke-width="1.5"><circle cx="12" cy="12" r="10"/><ellipse cx="12" cy="12" rx="4.5" ry="10"/><path d="M2 12h20M4 6.5h16M4 17.5h16M12 2v20"/></svg>
        </div>
      </div>
      <div class="contact__address">Street name City Name,<br>Zipcode,012345</div>
    </div>
  </section>

  <section class="card card--back">
    <div class="wordmark">pexla</div>
    <div class="back-url">www.pexla.com</div>
  </section>
</body>
</html>
```